WL Bundle Page Redesign Wordpress site

IMPORTANT: the design will need to look nice on mobile...so please keep that in mind!
We need to redesign our current Wordpress page to make it more appealing and look like an ecommerce page. We need the ability to implement this design on our Wordpress site.
Here is the current page: https://www.rlpalmerhealth.com/supplements/weight-loss-focus-bundle/
However, the reference sample of what it has to look like or complement is also attached.
Attached is the Word document is the copy for the new page and the FAQs text.
The color palette should match the bottles or look nice with all 3 bottles on the page.
Thanks!

Requirements
Should not have
• any random stock photography; use images provided

```html
<!DOCTYPE html>
<html lang="en">
<head>
<meta charset="utf-8">
<title>Weight Loss Bundle – Page Design</title>
<link href="https://fonts.googleapis.com/css2?family=Outfit:wght@400;500;600;700&family=Poppins:wght@400;500;600;700&display=swap" rel="stylesheet">
<style>
:root{
  --stage:#c8c8cc;
  --ink:#3f3552;
  --ink-soft:#5d566b;
  --body:#4a4652;
  --plum:#453a5e;
  --pink:#d4579b;
  --red:#e1253c;
  --blue:#2a3ca6;
  --mist:#f2f2f6;
  --lav:#f3f1fa;
  --white:#ffffff;
  --line:#d9d4e3;
}
*{box-sizing:border-box;margin:0;padding:0}
html,body{width:1058px;height:1200px;overflow:hidden;background:var(--stage)}
body{position:relative;font-family:"Poppins",sans-serif;color:var(--body)}
.panel{position:absolute;background:var(--white);overflow:hidden}
.p1{left:120px;top:70px;width:249px;height:1059px}
.p2{left:405px;top:70px;width:234px;height:1056px}
.p3{left:666px;top:70px;width:272px;height:875px}
.abs{position:absolute}
.h2{font-family:"Outfit",sans-serif;font-weight:500;color:var(--ink);line-height:1.12;letter-spacing:-.1px}
.center{text-align:center}
.rule{display:block;width:26px;height:0;border-top:.6px solid var(--ink);margin:4px auto 0}
.rule.left{margin-left:0}
.txt{font-size:3.3px;line-height:1.55;color:var(--body)}
.ph{position:absolute}
.round{border-radius:50%}
.btn{position:absolute;display:flex;align-items:center;justify-content:center;border-radius:20px;color:#fff;font-family:"Poppins",sans-serif;font-weight:600;font-size:4px;letter-spacing:.1px}
ul.dots{list-style:none}
ul.dots li{position:relative;padding-left:5px;margin-bottom:2.4px;font-size:3.2px;line-height:1.45}
ul.dots li::before{content:"";position:absolute;left:0;top:1.3px;width:1.8px;height:1.8px;border-radius:50%;background:currentColor}
ul.dots li b{display:block;font-weight:600;font-size:3.5px}
ul.dots li span{color:var(--body)}
.arrow{position:absolute;width:13px;height:13px;border-radius:50%;display:flex;align-items:center;justify-content:center}
.arrow.prev{background:#fff;border:.5px solid var(--line)}
.arrow.next{background:var(--plum)}
.video{position:absolute;border-radius:4px;background:linear-gradient(160deg,#8a7a74,#c9b9ad 55%,#e8e1dc)}
.play{position:absolute;left:50%;top:50%;width:12px;height:12px;margin:-6px 0 0 -6px;border:.8px solid #fff;border-radius:50%}
.play::after{content:"";position:absolute;left:4.3px;top:3px;border-left:4px solid #fff;border-top:2.6px solid transparent;border-bottom:2.6px solid transparent}
.pill{position:absolute;background:var(--plum);color:#fff;font-size:3.6px;font-weight:600;border-radius:10px;padding:1.6px 6px}
.step-title{position:absolute;font-family:"Outfit",sans-serif;font-weight:500;font-size:6px;line-height:1.15;color:var(--ink)}
.notice{font-size:3.2px;line-height:1.45}
.notice b{font-weight:600;color:var(--ink)}
.faq-item{position:absolute;left:131px;width:119px;height:9px;border:.5px solid var(--line);background:#fff;font-size:2.8px;color:var(--ink);display:flex;align-items:center;padding:0 4px;justify-content:space-between}
.faq-item i{font-style:normal;width:3.2px;height:3.2px;border-radius:50%;background:var(--plum);flex:none}
.logo{font-family:"Outfit",sans-serif;font-weight:700;color:var(--plum);letter-spacing:.2px}
</style>
</head>
<body>

<!-- ============ PANEL ONE ============ -->
<section class="panel p1">
  <header class="abs" style="left:0;top:0;width:249px;height:25px">
    <div class="abs logo" style="left:14px;top:8px;font-size:8px">RLPALMER</div>
    <div class="abs btn" style="left:180px;top:4px;width:29px;height:5px;background:#d88bc0;font-size:2.3px;font-weight:500">RL's Products</div>
    <div class="abs btn" style="left:211px;top:4px;width:25px;height:5px;background:var(--plum);font-size:2.3px">LOGIN</div>
    <nav class="abs" style="left:90px;top:13px;display:flex;gap:7px;font-size:2.3px;color:var(--ink-soft);align-items:center">
      <span style="background:var(--plum);color:#fff;padding:1px 4px;border-radius:1px">HOME</span>
      <span>SUCCESS STORIES</span><span>MEDIA ROOM</span><span>ABOUT</span><span>BLOGS</span><span>CONTACT US</span>
    </nav>
  </header>

  <section class="abs" style="left:0;top:25px;width:249px;height:150px;background:linear-gradient(180deg,#ececf1,#f3f3f6)">
    <div class="ph round" role="img" aria-label="Soft pink glow behind the three bundle bottles" style="left:95px;top:5px;width:110px;height:110px;background:radial-gradient(circle,#f7c6dc 0%,#f3dbe8 45%,rgba(243,243,246,0) 70%)"></div>
    <div class="ph" role="img" aria-label="Blood Sugar Reset, Liver Reset and Tummy Reset bottles" style="left:95px;top:38px;width:150px;height:90px;border-radius:8px;background:linear-gradient(90deg,#e9ecf6 0%,#f6eef4 50%,#f7e9ec 100%)"></div>
    <div class="abs h2" style="left:20px;top:37px;font-size:9.4px;font-weight:400;line-height:1.2">Get the Weight<br>Loss Bundle &amp;<br><b style="font-weight:600">Start Your<br>Transformation<br>Today!</b></div>
    <div class="btn" style="left:19px;top:97px;width:52px;height:15px;background:var(--plum);font-size:4.4px">SHOP NOW</div>
  </section>

  <section class="abs" style="left:0;top:175px;width:249px;height:166px">
    <div class="ph round" role="img" aria-label="Founder smiling, holding the three bundle bottles, framed in a purple circle" style="left:9px;top:16px;width:112px;height:112px;background:radial-gradient(circle at 40% 40%,#f0c6de,#b25fb0 60%,#7d4aa8)"></div>
    <h2 class="abs h2" style="left:133px;top:28px;width:112px;font-size:10.8px">The Ultimate Trio to Help you Burn Fat, Slim Down and See Faster Results*</h2>
    <span class="abs" style="left:133px;top:84px;width:26px;border-top:.6px solid var(--ink)"></span>
    <p class="abs txt" style="left:133px;top:95px;width:107px;text-align:justify;font-size:3.5px">Achieve your weight loss goals with the Weight Loss Bundle, a powerful combination of Tummy Reset, Liver Reset, and Blood Sugar Reset—designed to optimize digestion, detox your liver, and stabilize blood sugar for faster, healthier weight loss.</p>
  </section>

  <section class="abs" style="left:0;top:341px;width:249px;height:175px;background:var(--lav)">
    <div class="ph" role="img" aria-label="Smiling woman in a white sweater with the bundle bottles, in front of a pink-to-purple arch" style="left:120px;top:8px;width:121px;height:167px;border-radius:60px 60px 0 0;background:linear-gradient(180deg,#f2c3dd,#c9a5e3 55%,#8da0e6)"></div>
    <h2 class="abs h2" style="left:14px;top:13px;font-size:11px">Why Choose the<br>Weight Loss Bundle?</h2>
    <span class="abs" style="left:14px;top:42px;width:26px;border-top:.6px solid var(--ink)"></span>
    <p class="abs txt" style="left:14px;top:55px;width:105px;font-size:3px">● Losing weight isn't just about cutting calories—it's about supporting your body's natural fat-burning processes. This all-in-one bundle works synergistically to:</p>
    <ul class="abs dots" style="left:29px;top:75px;width:90px;color:var(--ink)">
      <li><b>Boost overall metabolism</b><span>Keep your body in fat-burning mode all day long</span></li>
      <li><b>Support liver detoxification</b><span>Eliminate toxins and accelerate the body's ability to burn fat (Liver Reset)</span></li>
      <li><b>Enhance digestion &amp; regularity</b><span>Flush out waste and improve nutrient absorption (Tummy Reset)</span></li>
      <li><b>Balance blood sugar</b><span>Prevent energy crashes and support fat loss (Blood Sugar Reset)</span></li>
    </ul>
    <p class="abs txt" style="left:14px;top:152px;width:105px;font-size:3px">● With this three-pronged approach, you'll break through weight loss plateaus, feel lighter, and stay energized!</p>
  </section>

  <section class="abs" style="left:0;top:516px;width:249px;height:543px">
    <h2 class="abs h2 center" style="left:0;top:24px;width:249px;font-size:11px">What's Inside the<br>Weight Loss Bundle?</h2>
    <span class="abs" style="left:112px;top:53px;width:26px;border-top:.6px solid var(--ink)"></span>

    <div class="ph round" role="img" aria-label="Tummy Reset bottles over a red radial glow" style="left:14px;top:72px;width:110px;height:110px;background:radial-gradient(circle,#fbe1e4 30%,#f4a8b3 60%,#fde9ec 72%,rgba(255,255,255,0) 73%)"></div>
    <div class="abs h2" style="left:128px;top:67px;font-size:8px;color:var(--red)">Tummy Reset</div>
    <div class="abs h2" style="left:128px;top:76px;font-size:6px">Gut Health &amp; Digestive Cleansing</div>
    <ul class="abs dots" style="left:143px;top:88px;width:100px;color:var(--red)">
      <li><b>Supports Healthy Digestion</b><span>Helps break down food more efficiently and absorb nutrients better for less bloating</span></li>
      <li><b>Cleanses the Digestive Tract</b><span>Promotes gentle detoxification to remove waste buildup and support a flatter tummy</span></li>
      <li><b>Relieves Occasional Constipation</b><span>Provides natural, non-habit-forming relief for digestive discomfort.</span></li>
      <li><b>Encourages a Balanced Gut Microbiome</b><span>Helps good bacteria thrive for overall gut health</span></li>
      <li><b>Fast-Acting Yet Gentle</b><span>Works effectively without cramping or urgency.</span></li>
    </ul>
    <div class="btn" style="left:128px;top:186px;width:58px;height:10px;background:var(--red);font-size:3.6px">LEARN MORE</div>

    <div class="abs h2" style="left:14px;top:213px;font-size:8px;color:var(--pink)">Liver Reset</div>
    <div class="abs h2" style="left:14px;top:222px;font-size:6px">Detox &amp; Fat Metabolism</div>
    <ul class="abs dots" style="left:24px;top:233px;width:100px;color:var(--pink)">
      <li><b>Boosts Your Body's Ability to Burn Unwanted Fat</b><span>A properly functioning liver helps your body process fat more efficiently, supporting healthy weight loss.</span></li>
      <li><b>Promotes Digestive Health</b><span>Supports optimal bile production for better digestion and nutrient absorption</span></li>
      <li><b>Supports Liver Detoxification</b><span>Helps flush out toxins, promoting a healthy and efficient liver</span></li>
      <li><b>Protects Against Toxins &amp; Free Radicals</b><span>Packed with antioxidants that help defend against oxidative stress</span></li>
      <li><b>Enhances Overall Health</b><span>A clean, healthy liver means better energy, clearer skin, and improved well-being</span></li>
    </ul>
    <div class="btn" style="left:14px;top:343px;width:58px;height:10px;background:var(--pink);font-size:3.6px">LEARN MORE</div>
    <div class="ph round" role="img" aria-label="Liver Reset bottles over a pink radial glow" style="left:125px;top:221px;width:115px;height:115px;background:radial-gradient(circle,#fbe6f1 30%,#efb0d1 60%,#fbecf4 72%,rgba(255,255,255,0) 73%)"></div>

    <div class="ph round" role="img" aria-label="Blood Sugar Reset bottles over a blue radial glow" style="left:14px;top:390px;width:112px;height:112px;background:radial-gradient(circle,#e5e9fa 30%,#b6c1ee 60%,#eef0fb 72%,rgba(255,255,255,0) 73%)"></div>
    <div class="abs h2" style="left:128px;top:376px;font-size:8px;color:var(--blue)">Blood Sugar Reset</div>
    <div class="abs h2" style="left:128px;top:385px;font-size:6px">Stabilize &amp; Support Fat Loss</div>
    <ul class="abs dots" style="left:143px;top:397px;width:100px;color:var(--blue)">
      <li><b>Naturally increase GLP-1 levels</b><span>(with clinically-tested ingredients) so you eat less and stay full longer, reducing appetite*</span></li>
      <li><b>Support fat loss, accelerate fat burning and reduce body weight</b><span>including visceral (belly) fat, when combined with a healthy lifestyle (Lose Fat, Not Muscle)*</span></li>
      <li><b>By boosting GLP-1</b><span>your body sends signals to the brain that reduce cravings, quiet food noise, and help you feel full longer—naturally.*</span></li>
      <li><b>For anyone who wants fast, healthy weight loss</b><span>as well as for diabetics, pre-diabetics, and those with insulin resistance*</span></li>
      <li><b>Support healthy blood sugar levels</b><span>to prevent your body from storing fat and to reduce food cravings, especially for carbs and sugar*</span></li>
    </ul>
    <div class="btn" style="left:128px;top:512px;width:58px;height:10px;background:var(--blue);font-size:3.6px">LEARN MORE</div>
  </section>
</section>

<!-- ============ PANEL TWO ============ -->
<section class="panel p2">
  <section class="abs" style="left:0;top:0;width:234px;height:157px;background:var(--mist)">
    <h2 class="abs h2 center" style="left:0;top:16px;width:234px;font-size:11px">Real People, Real Results</h2>
    <span class="abs" style="left:104px;top:34px;width:26px;border-top:.6px solid var(--ink)"></span>
    <div class="video" role="img" aria-label="Customer video testimonial with bundle bottles" style="left:13px;top:44px;width:66px;height:74px"><i class="play"></i></div>
    <div class="video" role="img" aria-label="Customer video testimonial with bundle bottles" style="left:85px;top:44px;width:65px;height:74px"><i class="play"></i></div>
    <div class="video" role="img" aria-label="Customer video testimonial with bundle bottles" style="left:155px;top:44px;width:66px;height:74px"><i class="play"></i></div>
    <div class="arrow prev" style="left:103px;top:128px"><svg width="6" height="4" viewBox="0 0 6 4"><path d="M6 2H1M2.5 .5L1 2l1.5 1.5" stroke="#3f3552" stroke-width=".6" fill="none"/></svg></div>
    <div class="arrow next" style="left:118px;top:128px"><svg width="6" height="4" viewBox="0 0 6 4"><path d="M0 2h5M3.5 .5L5 2 3.5 3.5" stroke="#fff" stroke-width=".6" fill="none"/></svg></div>
  </section>

  <section class="abs" style="left:0;top:157px;width:234px;height:156px">
    <h2 class="abs h2 center" style="left:0;top:17px;width:234px;font-size:10.5px">Who Is the Weight Loss Bundle For?</h2>
    <span class="abs" style="left:104px;top:32px;width:26px;border-top:.6px solid var(--ink)"></span>
    <div class="ph round" role="img" aria-label="Customer in a cap holding the three bundle bottles, in a circle frame" style="left:14px;top:45px;width:89px;height:89px;border:.6px solid #e88aa8;background:radial-gradient(circle at 45% 40%,#f4e6da,#cfa58c 60%,#f2d5de)"></div>
    <ul class="abs dots" style="left:117px;top:122px;width:0"></ul>
    <ul class="abs dots" style="left:117px;top:122px"></ul>
    <ul class="abs dots" style="left:117px;top:124px"></ul>
    <ul class="abs dots" style="left:117px;top:124px"></ul>
    <ul class="abs dots" style="left:117px;top:46px;width:107px;color:var(--ink);font-weight:600">
      <li>Anyone struggling with slow weight loss?</li>
      <li>Those dealing with bloating, sluggish digestion, or irregularity</li>
      <li>Individuals looking to detox and boost their metabolism</li>
      <li>People who experience sugar cravings, energy crashes, or blood sugar spikes</li>
      <li>Anyone who wants a natural, science-backed way to support weight management</li>
    </ul>
    <p class="abs txt" style="left:107px;top:117px;width:117px;font-size:2.9px">● This bundle is your ultimate weight loss support system—helping you reset your metabolism, cleanse your system, and shed stubborn fat.</p>
  </section>

  <section class="abs" style="left:0;top:313px;width:234px;height:184px;background:var(--lav)">
    <div class="ph" role="img" aria-label="Smiling woman in a sheer black top with the bundle bottles, in front of a pink arch" style="left:118px;top:-6px;width:112px;height:190px;border-radius:56px 56px 0 0;background:linear-gradient(180deg,#f3c4dd,#d9b4e6 50%,#a9b3ea)"></div>
    <h2 class="abs h2" style="left:13px;top:16px;font-size:10px">Powerful Ingredients,<br>Backed by Science</h2>
    <span class="abs" style="left:13px;top:40px;width:26px;border-top:.6px solid var(--ink)"></span>
    <p class="abs txt" style="left:13px;top:50px;width:100px;font-size:3px">Each product in the Weight Loss Bundle is formulated based on scientific research:</p>
    <div class="abs txt" style="left:13px;top:63px;width:104px;font-size:2.9px;text-align:justify">
      <p style="padding-left:7px;margin-bottom:3px">● <b style="color:var(--ink);font-size:3.3px">The Magnesium Oxide blend in Tummy Reset</b> promotes gentle and effective colon cleansing, helping clear waste buildup for better digestion and improved gut health. Magnesium is clinically recognized for its ability to aid digestion, regulate bowel movements, and prevent bloating.</p>
      <p style="padding-left:7px;margin-bottom:3px">● <b style="color:var(--ink);font-size:3.3px">Milk Thistle in Liver Reset</b> supports liver detoxification and enhances fat metabolism, crucial for weight loss and overall wellness. Studies suggest it may help improve liver function and protect against damage caused by toxins, alcohol, and fatty liver disease.</p>
      <p style="padding-left:7px">● <b style="color:var(--ink);font-size:3.3px">Citrulin® in Blood Sugar Reset</b> has been shown to increase GLP-1, a hormone that plays a crucial role in blood sugar regulation and appetite control. It has been clinically researched for its role in supporting healthy blood sugar levels and metabolic function.</p>
    </div>
  </section>

  <section class="abs" style="left:0;top:497px;width:234px;height:130px">
    <div class="video" role="img" aria-label="Customer video testimonial with bundle bottles" style="left:13px;top:24px;width:66px;height:74px"><i class="play"></i></div>
    <div class="video" role="img" aria-label="Customer video testimonial with bundle bottles" style="left:85px;top:24px;width:65px;height:74px;background:linear-gradient(160deg,#4f74b7,#b7c6e4 60%,#e5e8f2)"><i class="play"></i></div>
    <div class="video" role="img" aria-label="Customer video testimonial with bundle bottles" style="left:155px;top:24px;width:66px;height:74px"><i class="play"></i></div>
    <div class="arrow prev" style="left:103px;top:107px"><svg width="6" height="4" viewBox="0 0 6 4"><path d="M6 2H1M2.5 .5L1 2l1.5 1.5" stroke="#3f3552" stroke-width=".6" fill="none"/></svg></div>
    <div class="arrow next" style="left:118px;top:107px"><svg width="6" height="4" viewBox="0 0 6 4"><path d="M0 2h5M3.5 .5L5 2 3.5 3.5" stroke="#fff" stroke-width=".6" fill="none"/></svg></div>
  </section>

  <section class="abs" style="left:0;top:627px;width:234px;height:429px">
    <h2 class="abs h2 center" style="left:0;top:4px;width:234px;font-size:10.5px">What to Expect When Taking the<br>Weight Loss Bundle</h2>
    <p class="abs txt center" style="left:28px;top:43px;width:178px;font-size:3.3px;letter-spacing:-.05px">The Weight Loss Bundle (Blood Sugar Reset, Liver Reset, and Tummy Reset) is designed to work synergistically to support fat metabolism, balance blood sugar, detoxify the liver, and optimize digestion. Here's what you can expect over three months with consistent use:</p>

    <div class="pill" style="left:14px;top:82px">WEEK 1-4</div>
    <div class="step-title" style="left:53px;top:80px">Kickstarting Fat Burning<br>&amp; Detoxification</div>
    <div class="ph round" role="img" aria-label="Customer smiling with the bundle bottles, circle frame" style="left:133px;top:72px;width:87px;height:87px;border:.6px solid #a6b0e6;background:radial-gradient(circle at 45% 40%,#e7d2c2,#9c7d69 60%,#ded6e8)"></div>
    <ul class="abs dots" style="left:28px;top:104px;width:100px;color:var(--ink)">
      <li><b>Liver Reset</b><span>supports liver detox, allowing for more efficient fat metabolism</span></li>
      <li><b>Blood Sugar Reset</b><span>helps stabilize blood sugar levels, reducing cravings and energy crashes</span></li>
      <li><b>Tummy Reset</b><span>promotes regularity and digestive cleansing to help eliminate waste buildup</span></li>
    </ul>
    <p class="abs notice" style="left:13px;top:152px;width:130px">● <b>What you may notice</b><br><span style="padding-left:6px">Less bloating, improved digestion, and fewer sugar cravings. Some may begin to experience gradual weight loss as the body adjusts.</span></p>

    <div class="ph round" role="img" aria-label="Customer holding the bundle bottles, circle frame" style="left:13px;top:188px;width:78px;height:78px;border:.6px solid #a6b0e6;background:radial-gradient(circle at 45% 40%,#efe0d6,#b89681 60%,#e6e2ee)"></div>
    <div class="pill" style="left:99px;top:192px">MONTH 2</div>
    <div class="step-title" style="left:138px;top:190px">Accelerated Fat Loss<br>&amp; Enhanced Metabolism</div>
    <ul class="abs dots" style="left:114px;top:212px;width:105px;color:var(--ink)">
      <li><span>The liver is more efficient at processing fat and removing toxins</span></li>
      <li><span>More stable blood sugar levels help curb appetite and reduce fat storage</span></li>
      <li><span>Gut health improves, leading to better digestion and nutrient absorption</span></li>
    </ul>
    <p class="abs notice" style="left:99px;top:243px;width:125px">● <b>What you may notice</b><br><span style="padding-left:6px">More sustained energy, a noticeable reduction in bloating, and steady weight loss as metabolism improves.</span></p>

    <div class="pill" style="left:14px;top:290px">MONTH 3</div>
    <div class="step-title" style="left:53px;top:288px">Sustained Weight Loss &amp;<br>Long-Term Balance</div>
    <div class="ph round" role="img" aria-label="Customer in a visor holding the bundle bottles, circle frame" style="left:139px;top:283px;width:79px;height:79px;border:.6px solid #e88aa8;background:radial-gradient(circle at 45% 40%,#dfe6f4,#6f8cc6 60%,#eadce8)"></div>
    <ul class="abs dots" style="left:28px;top:314px;width:100px;color:var(--ink)">
      <li><span>Liver function is optimized, supporting continued fat metabolism</span></li>
      <li><span>Balanced blood sugar levels help maintain a steady weight and prevent crashes</span></li>
      <li><span>A clean and balanced gut promotes long-term digestive health</span></li>
    </ul>
    <p class="abs notice" style="left:13px;top:345px;width:125px">● <b>What you may notice</b><br><span style="padding-left:6px">A leaner, more energized feeling with consistent weight loss, fewer cravings, and improved digestion.</span></p>

    <div class="abs" style="left:13px;top:386px;width:209px;height:32px;border:.6px solid #b9a7d6;border-radius:4px;background:linear-gradient(90deg,#f4f1fb,#fbe9f0)"></div>
    <div class="pill" style="left:93px;top:380px;font-size:4px;padding:2px 6px">For best results</div>
    <p class="abs txt center" style="left:25px;top:396px;width:185px;font-size:3.8px;color:var(--ink-soft)">Stay hydrated, maintain a balanced diet, and stay active while using the Weight Loss Bundle for long-term success!</p>
  </section>
</section>

<!-- ============ PANEL THREE ============ -->
<section class="panel p3">
  <section class="abs" style="left:0;top:0;width:272px;height:254px">
    <h2 class="abs h2 center" style="left:0;top:15px;width:272px;font-size:12px">Testimonials</h2>
    <span class="abs" style="left:123px;top:35px;width:26px;border-top:.6px solid var(--ink)"></span>
    <div class="ph" role="img" aria-label="Before photo of a customer" style="left:16px;top:50px;width:57px;height:93px;background:linear-gradient(180deg,#b3aa9e,#8c8478)"></div>
    <div class="ph" role="img" aria-label="After photo of a customer" style="left:74px;top:50px;width:57px;height:93px;background:linear-gradient(180deg,#c2c8c9,#9a9a96)"></div>
    <div class="ph" role="img" aria-label="Before photo of a customer" style="left:142px;top:50px;width:57px;height:93px;background:linear-gradient(180deg,#8e9a87,#5f6256)"></div>
    <div class="ph" role="img" aria-label="After photo of a customer" style="left:200px;top:50px;width:57px;height:93px;background:linear-gradient(180deg,#b6b0a7,#7c8a72)"></div>
    <div class="abs" style="left:16px;top:133px;width:115px;height:10px;background:rgba(60,55,80,.75)"></div>
    <div class="abs" style="left:142px;top:133px;width:115px;height:10px;background:rgba(60,55,80,.75)"></div>
    <span class="abs" style="left:37px;top:135px;font-size:4px;color:#fff">Before</span>
    <span class="abs" style="left:97px;top:135px;font-size:4px;color:#fff">After</span>
    <span class="abs" style="left:163px;top:135px;font-size:4px;color:#fff">Before</span>
    <span class="abs" style="left:223px;top:135px;font-size:4px;color:#fff">After</span>
    <div class="abs h2" style="left:16px;top:152px;font-size:5.5px">Carla says</div>
    <div class="abs h2" style="left:142px;top:152px;font-size:5.5px">Denise says</div>
    <p class="abs txt" style="left:16px;top:160px;width:115px;font-size:3px">"When I began, I weighed 224 pounds and the unhappiest I've ever been. I purchased Liver Reset and began with two capsules at bedtime and after a few weeks increased to 3 caps at bedtime. I did green smoothie cleanse, ate clean and shed a total of 55 pounds. Current weight is 169, feeling more energized and stronger everyday."</p>
    <p class="abs txt" style="left:142px;top:160px;width:115px;font-size:3px;text-align:justify">"The trio supplements (Liver Reset, Blood Sugar Reset and Tummy Reset) has been instrumental in helping me lose belly fat, inches and better controlled sugars! Just unbelievable! I've gone from a size 16 to a size 12 and these are a bit loose, and from XL in blouses to a medium! My A1c from an 8.2 to a 6.2. I'm so proud of myself and am feeling alive again, moving, laughing, and feeling happy!"</p>
    <div class="arrow prev" style="left:120px;top:219px"><svg width="6" height="4" viewBox="0 0 6 4"><path d="M6 2H1M2.5 .5L1 2l1.5 1.5" stroke="#3f3552" stroke-width=".6" fill="none"/></svg></div>
    <div class="arrow next" style="left:138px;top:219px"><svg width="6" height="4" viewBox="0 0 6 4"><path d="M0 2h5M3.5 .5L5 2 3.5 3.5" stroke="#fff" stroke-width=".6" fill="none"/></svg></div>
  </section>

  <section class="abs" style="left:0;top:254px;width:272px;height:213px;background:linear-gradient(180deg,#f4f3f9,#f8f7fb)">
    <div class="ph round" role="img" aria-label="Soft lavender glow behind the bundle bottles" style="left:8px;top:35px;width:100px;height:100px;background:radial-gradient(circle,#e7def4 40%,rgba(244,243,249,0) 70%)"></div>
    <div class="ph" role="img" aria-label="Blood Sugar Reset, Liver Reset and Tummy Reset bottles" style="left:20px;top:31px;width:90px;height:131px;border-radius:6px;background:linear-gradient(180deg,#eef0f8,#f4e7ef 60%,#ece6f3)"></div>
    <h2 class="abs h2" style="left:131px;top:14px;font-size:12px">Frequently Asked<br>Questions</h2>
    <span class="abs" style="left:131px;top:45px;width:26px;border-top:.6px solid var(--ink)"></span>
    <div class="faq-item" style="top:59px"><span>01 What are the benefits of the Weight Loss Bundle?</span><i></i></div>
    <div class="faq-item" style="top:71px;background:var(--plum);color:#fff;border-color:var(--plum)"><span>02 Do we really need to take Tummy Reset at bedtime?</span><i style="background:#fff"></i></div>
    <div class="abs" style="left:131px;top:80px;width:119px;height:22px;border:.5px solid var(--plum);background:#fff;padding:2px 4px;font-size:2.4px;line-height:1.45;color:var(--body)">We do recommend taking Tummy Reset at bedtime so you have a satisfying result by morning. If you take it during the day, you may need to go at an inconvenient time. Additionally, it's important to take with 10-12 ounces of water to help it work more effectively.</div>
    <div class="faq-item" style="top:106px"><span>03 How to Use the Weight Loss Bundle?</span><i></i></div>
    <div class="faq-item" style="top:117px;height:11px;align-items:center"><span>04 Who is Blood Sugar Reset for? Is it just for diabetics and pre-diabetics?</span><i></i></div>
    <div class="faq-item" style="top:130px"><span>05 What are the side effects Liver Reset since it's a detox?</span><i></i></div>
    <div class="faq-item" style="top:141px"><span>06 What are the ingredients for Liver Reset?</span><i></i></div>
    <div class="faq-item" style="top:152px"><span>07 What are the ingredients for Blood Sugar Reset?</span><i></i></div>
    <div class="btn" style="left:160px;top:172px;width:61px;height:11px;background:var(--plum);font-size:3.6px;font-weight:500">VIEW MORE FAQ's</div>
  </section>

  <section class="abs" style="left:0;top:467px;width:272px;height:204px;background:linear-gradient(115deg,#e96f96 0%,#c46bb0 45%,#8b6fc6 100%)">
    <div class="ph" role="img" aria-label="Smiling woman in a white top holding a bundle bottle" style="left:168px;top:-16px;width:104px;height:220px;background:linear-gradient(180deg,rgba(255,255,255,0) 0%,rgba(250,228,238,.55) 40%,rgba(245,230,245,.35) 100%)"></div>
    <h2 class="abs h2" style="left:15px;top:16px;font-size:14px;font-weight:600;color:#fff;line-height:1.15">Still Unsure If the<br>Weight Loss Bundle<br>Is Right for You?</h2>
    <p class="abs" style="left:16px;top:87px;width:105px;font-size:3.6px;line-height:1.4;color:#fff">We get it—choosing the right supplements is a big decision! That's why we're offering</p>
    <div class="abs round" role="img" aria-label="Money-back guarantee seal" style="left:118px;top:79px;width:44px;height:44px;background:radial-gradient(circle,#f6c531 55%,#d99a12 56%,#f3bd2a 68%,#c88b10 70%)"></div>
    <div class="abs" style="left:16px;top:108px;font-family:'Outfit',sans-serif;font-weight:700;font-size:9px;color:#fff;line-height:1.1">10% OFF YOUR FIRST<br>ORDER <span style="font-size:4px;font-weight:400">when you</span> <u style="font-size:7.5px">subscribe today</u></div>
    <p class="abs" style="left:16px;top:134px;font-size:6.5px;font-weight:600;color:#fff;font-family:'Outfit',sans-serif">Have questions? <span style="font-size:4px;font-weight:400">Our team is here to help.</span></p>
    <div class="btn" style="left:15px;top:152px;width:139px;height:29px;border:1px solid #fff;background:var(--plum);font-family:'Outfit',sans-serif;font-size:6.8px;font-weight:500;text-align:center;line-height:1.25">Get the Weight Loss Bundle &amp;<br>Start Your Transformation Today!</div>
  </section>

  <section class="abs" style="left:0;top:671px;width:272px;height:146px">
    <h2 class="abs h2 center" style="left:0;top:20px;width:272px;font-size:12px">Customer Reviews</h2>
    <span class="abs" style="left:123px;top:39px;width:26px;border-top:.6px solid var(--ink)"></span>
    <p class="abs center" style="left:0;top:58px;width:272px;font-family:'Outfit',sans-serif;font-size:15px;line-height:1.2;color:#e6e3ea">SPACE FOR<br>REVIEWLY REVIEWS</p>
  </section>

  <footer class="abs" style="left:0;top:817px;width:272px;height:58px;background:linear-gradient(90deg,#e9e3f5,#f6dfee 60%,#f9dfe6)">
    <div class="abs logo center" style="left:0;top:15px;width:272px;font-size:8px">RLPALMER</div>
    <div class="abs" style="left:45px;top:32px;display:flex;gap:10px;font-size:2.6px;color:var(--ink);line-height:1.3">
      <div style="display:flex;gap:3px"><svg width="5" height="5" viewBox="0 0 5 5"><rect width="5" height="5" rx="1" fill="#453a5e"/><path d="M1.4 1.2l.7.7-.4.5a2 2 0 0 0 .9.9l.5-.4.7.7-.5.5c-1.3 0-2.4-1.1-2.4-2.4z" fill="#fff"/></svg><span>CALL US<br>(555) 014-2290</span></div>
      <div style="display:flex;gap:3px"><svg width="5" height="5" viewBox="0 0 5 5"><rect width="5" height="5" rx="1" fill="#453a5e"/><path d="M1 1.5h3v2H1zM1 1.5l1.5 1.2L4 1.5" stroke="#fff" stroke-width=".35" fill="none"/></svg><span>EMAIL US<br>info@websitename.com</span></div>
      <div style="display:flex;gap:3px"><svg width="5" height="5" viewBox="0 0 5 5"><rect width="5" height="5" rx="1" fill="#453a5e"/><path d="M2.5 1a1 1 0 0 1 1 1c0 .8-1 2-1 2s-1-1.2-1-2a1 1 0 0 1 1-1z" fill="#fff"/></svg><span>Palmer Wellness 400 Harbor Lane Suite 12<br>Fairview, MD 20700</span></div>
    </div>
    <span class="abs" style="left:16px;top:45px;width:240px;border-top:.4px solid #cfc6dd"></span>
    <nav class="abs" style="left:0;top:49px;width:272px;display:flex;justify-content:center;gap:10px;font-size:2.4px;color:var(--ink)">
      <span>HOME</span><span>SUCCESS STORIES</span><span>MEDIA ROOM</span><span>ABOUT</span><span>BLOGS</span><span>CONTACT US</span>
    </nav>
  </footer>
  <div class="abs" style="left:0;top:863px;width:272px;height:12px;background:var(--plum)">
    <span class="abs" style="left:16px;top:4px;font-size:2.2px;color:#d8d2e4">Copyright © 2025. All Rights Reserved By Company name</span>
    <div class="abs" style="left:229px;top:3px;display:flex;gap:1.5px">
      <i style="width:5px;height:5px;border:.4px solid #fff;border-radius:1px"></i>
      <i style="width:5px;height:5px;border:.4px solid #fff;border-radius:1px"></i>
      <i style="width:5px;height:5px;border:.4px solid #fff;border-radius:1px"></i>
      <i style="width:5px;height:5px;border:.4px solid #fff;border-radius:1px"></i>
    </div>
  </div>
</section>

</body>
</html>
```